Brivolt Technologies business card design

We need a business card designed with our new logo. it would be great if the card could communicate it is a technology based company.

Target Market(s)

system integrators

Industry/Entity Type

technology, IOT

Contact Information for Business Card

Name, designation, Address, telephone number, email address

Requirements
Must have
• logo and company name
Nice to have
• something to do with technology

```html
<!DOCTYPE html>
<html lang="en">
<head>
<meta charset="utf-8">
<title>Brivolt Technologies Business Card</title>
<link rel="stylesheet" href="https://fonts.googleapis.com/css2?family=Open+Sans:ital,wght@0,400;0,700;0,800;1,400&display=swap">
<style>
  :root {
    --stage: #2a2a2a;
    --card: #1b1b1b;
    --card-shade: #222222;
    --orange: #f7931e;
    --white: #ffffff;
    --muted: #d8d8d8;
  }
  * { box-sizing: border-box; margin: 0; padding: 0; }
  html, body { width: 1200px; height: 900px; overflow: hidden; }
  body {
    background: var(--stage);
    font-family: "Open Sans", Arial, sans-serif;
    display: flex;
    flex-direction: column;
    align-items: center;
    justify-content: center;
    gap: 40px;
  }
  .card {
    position: relative;
    width: 660px;
    height: 377px;
    background: var(--card);
    border-bottom: 3px solid var(--orange);
    border-right: 3px solid var(--orange);
    box-shadow: 0 14px 30px rgba(0,0,0,.45);
    overflow: hidden;
  }
  .wordmark {
    display: flex;
    align-items: center;
    gap: 12px;
    color: var(--white);
    font-weight: 800;
    text-transform: uppercase;
    letter-spacing: 1px;
  }
  .wordmark-square {
    width: 22px;
    height: 22px;
    background: var(--orange);
    flex: none;
  }
  .card-front .wordmark { position: absolute; left: 48px; top: 50px; font-size: 30px; }
  .front-accent {
    position: absolute;
    right: -40px;
    top: 90px;
    width: 320px;
    height: 260px;
    background: linear-gradient(135deg, var(--card-shade), var(--card));
  }
  .holder { position: absolute; left: 48px; top: 140px; }
  .holder-name {
    color: var(--orange);
    font-weight: 800;
    font-size: 22px;
    text-transform: uppercase;
  }
  .holder-title { color: var(--white); font-style: italic; font-size: 15px; margin-top: 2px; }
  .contacts {
    position: absolute;
    left: 48px;
    top: 215px;
    list-style: none;
    color: var(--muted);
    font-size: 15px;
    line-height: 27px;
  }
  .contacts li { display: flex; align-items: center; gap: 10px; }
  .contacts svg { width: 14px; height: 14px; fill: var(--orange); flex: none; }
  .address {
    position: absolute;
    right: 48px;
    bottom: 40px;
    color: var(--white);
    font-size: 15px;
    line-height: 23px;
    text-align: right;
  }
  .back-pattern {
    position: absolute;
    inset: 0;
    background: linear-gradient(135deg, #1e1e1e 0%, #262626 50%, #1a1a1a 100%);
  }
  .card-back .wordmark { position: absolute; right: 44px; bottom: 40px; font-size: 22px; }
</style>
</head>
<body>
  <section class="card card-front">
    <div class="front-accent" role="img" aria-label="Faint large brand symbol decoration"></div>
    <div class="wordmark"><span class="wordmark-square"></span>Brivolt Technologies</div>
    <div class="holder">
      <p class="holder-name">Daren Holloway</p>
      <p class="holder-title">President</p>
    </div>
    <ul class="contacts">
      <li><svg viewBox="0 0 16 16"><path d="M3.5 1l3 3-2 2c1 2 3 4 5 5l2-2 3 3-2 2.5C7 14 2 9 1 3.5z"/></svg>555-318-0472</li>
      <li><svg viewBox="0 0 16 16"><path d="M1 3h14v10H1z M1 3l7 6 7-6" fill="none" stroke="#f7931e" stroke-width="1.6"/></svg>info@brivolttechnologies.com</li>
      <li><svg viewBox="0 0 16 16"><circle cx="8" cy="8" r="7"/><path d="M1 8h14M8 1c3 3 3 11 0 14M8 1c-3 3-3 11 0 14" fill="none" stroke="#1b1b1b" stroke-width="1"/></svg>www.brivolttechnologies.com</li>
    </ul>
    <p class="address">18420 Harbor Crest Dr<br>Seacliff CA 92600</p>
  </section>

  <section class="card card-back">
    <div class="back-pattern" role="img" aria-label="Tonal repeating brand symbol pattern"></div>
    <div class="wordmark"><span class="wordmark-square"></span>Brivolt Technologies</div>
  </section>
</body>
</html>
```